Ledger Lanternfox Powerpoint with Marshal Valorline Type Theme

Need powerpoint template with matching colors and different slide options. Logo and colors to be used can be found at ledgerlanternfox.example. Want brightly colored slide deck that is readable form the back of a room, but highlights colors. I will be incorporating Quizzap into the slides to gamify my presentations.

Target Market(s)

Tech

Industry/Entity Type

IT, specifically database, but crossing over to mental health in IT, important note this is not for a company, this is just for a professional building a brand

Font styles to use
Sans Serif

Colors
0054AA
0677BA
7BADD7
CADEEF
E8F1F8
EB3D1F
EC4F4E
F09395
F8D3D4
FCEDEE

Requirements
Must have
• My Logo in the bottom corner, front page, a thank your page, question page, content page, content page with two columns, content page with graphs, and icons to be used in the primary colors of the logos, About Me Page, Break Slides, Demo break slide
Should not have
• Lighter shades of colors, I want to pop out where colors are used, I want spacing and font size to be readable from the back of a room, most likely black text and white background

```html
<!DOCTYPE html>
<html lang="en">
<head>
<meta charset="utf-8">
<title>Ledger Lanternfox – Presentation Theme</title>
<link href="https://fonts.googleapis.com/css2?family=Poppins:wght@300;400;500;600;700&display=swap" rel="stylesheet">
<style>
:root{
  --navy:#1f4182;
  --navy-deep:#173466;
  --red:#e8312c;
  --ink:#2a2a2a;
  --gray:#7d7d7d;
  --dark:#3e3e3e;
  --mid:#8a8a8a;
  --line:#e4e4e4;
  --pale:#e4eaf3;
  --canvas:#e8e8ec;
  --white:#ffffff;
}
*{box-sizing:border-box}
html,body{margin:0;width:1200px;height:3630px;overflow:hidden;background:var(--canvas);font-family:'Poppins',sans-serif;color:var(--ink)}
.deck{display:grid;grid-template-columns:repeat(3,387px);grid-auto-rows:218px;column-gap:9px;row-gap:8px;padding:11px}
.slide{position:relative;overflow:hidden;background:var(--white)}
.bg-navy{background:var(--navy)}
.bg-dark{background:var(--dark)}
.bg-red{background:var(--red)}
.photo{position:absolute;inset:0}
.photo-city{background:linear-gradient(135deg,#2c5294 0%,#1d3b74 55%,#152f60 100%)}
.photo-desk{background:linear-gradient(160deg,#3b5f9b 0%,#253f70 50%,#6b7790 100%)}
.abs{position:absolute}
.brand{display:inline-flex;align-items:center;gap:4px;font-weight:700;font-size:9px;color:var(--navy);white-space:nowrap;line-height:1}
.brand::before{content:"";width:12px;height:12px;border-radius:50%;background:currentColor;flex:none}
.brand.on-dark{color:var(--white)}
.brand.red{color:var(--red)}
.rail{position:absolute;top:0;right:0;bottom:0;width:22px;border-left:1px solid var(--line)}
.rail::before{content:"";position:absolute;top:6px;left:6px;width:10px;height:10px;border-radius:50%;background:var(--navy)}
.rail span{position:absolute;top:50%;left:50%;transform:translate(-50%,-50%) rotate(90deg);font-size:6px;font-weight:700;color:var(--red);white-space:nowrap}
.rail.left{right:auto;left:0;border-left:0;border-right:1px solid var(--line)}
.rail.left span{transform:translate(-50%,-50%) rotate(-90deg)}
.rail.dark{border-color:rgba(255,255,255,.18)}
.rail.dark::before{background:var(--white)}
.rail.dark span{color:var(--white)}
.num{position:absolute;bottom:4px;right:27px;font-size:5px;color:#9a9a9a}
.num.ll{right:auto;left:6px}
.dash{position:absolute;width:16px;height:3px;background:var(--red)}
.h-title{position:absolute;top:18px;left:0;right:22px;margin:0;text-align:center;font-size:16px;font-weight:600;color:var(--navy)}
.h-title::after{content:"";display:block;width:14px;height:2px;background:var(--red);margin:4px auto 0}
.h-left{position:absolute;margin:0;font-size:16px;font-weight:600;color:var(--navy)}
.h-left::after{content:"";display:block;width:14px;height:2px;background:var(--red);margin-top:3px}
.fine{font-size:4.5px;line-height:1.45;color:#777;margin:0}
.fine.w{color:rgba(255,255,255,.85)}
.pill{display:inline-block;background:var(--red);color:var(--white);border-radius:10px;font-size:6px;font-weight:600;padding:3px 14px}
.faint-name{position:absolute;font-weight:700;color:#e3e8f1;white-space:nowrap}
.card{position:absolute;border-radius:3px;color:var(--white);text-align:center;padding:22px 6px 6px}
.card b{display:block;font-size:5.5px;font-weight:600;margin-bottom:3px}
.card p{font-size:4.2px;line-height:1.45;margin:0;opacity:.9}
table.grid{border-collapse:collapse;font-size:4.5px}
.q-mark{font-size:26px;font-weight:700;color:var(--red);line-height:.8}
.icon-sheet symbol *{vector-effect:non-scaling-stroke}
</style>
</head>
<body>
<main class="deck">

<section class="slide">
  <div class="photo photo-city" role="img" aria-label="Dark blue photo of a city and office setting behind the title"></div>
  <div class="abs" style="top:26px;left:0;right:0;text-align:center">
    <span class="brand on-dark">Ledger Lanternfox</span>
    <p class="fine w" style="margin-top:6px">www.ledgerlanternfox.example</p>
    <h1 style="margin:10px 0 0;color:#fff;font-size:25px;line-height:1;font-weight:600">Presentation<br>Title Goes Here</h1>
    <p style="margin:4px 0 0;color:#fff;font-size:7px">Sub Title Goes Here</p>
    <span class="pill" style="margin-top:14px">Oct 2021</span>
  </div>
</section>

<section class="slide bg-navy">
  <div class="photo photo-city" role="img" aria-label="Faded blue office photo behind the title" style="bottom:38px;opacity:.9"></div>
  <div class="abs" style="left:18px;top:70px;color:#fff">
    <h1 style="margin:0;font-size:21px;line-height:1.15;font-weight:500">TITLE OF<br>PRESENTATION</h1>
    <p class="fine w" style="margin-top:10px">Here is A place for Credentials<br>Date: 2021 March</p>
  </div>
  <div class="abs" style="left:0;right:0;bottom:0;height:38px;background:#fff;display:flex;align-items:center;justify-content:space-between;padding:0 18px 0 10px">
    <span class="brand">Ledger Lanternfox</span>
    <span style="font-size:5px;font-weight:600;color:var(--navy)">Presenter Name</span>
  </div>
</section>

<section class="slide">
  <div class="photo photo-city" role="img" aria-label="Blue toned photo of server racks"></div>
  <div class="abs" style="left:24px;top:58px;color:#fff">
    <span class="brand on-dark">Ledger Lanternfox</span>
    <h1 style="margin:10px 0 0;font-size:21px;line-height:1.15;font-weight:500">TITLE OF<br>PRESENTATION</h1>
    <p class="fine w" style="margin-top:10px">Here is A place for Credentials<br>Date: 2021 March</p>
  </div>
</section>

<section class="slide">
  <div class="photo photo-desk" role="img" aria-label="Photo of a laptop on a desk with a hand on the keyboard"></div>
  <div class="abs" style="left:38px;top:42px;background:#fff;padding:6px 10px;border-radius:2px"><span class="brand red">Ledger Lanternfox</span></div>
  <div class="abs" style="left:100px;right:0;top:118px;height:62px;background:var(--red);clip-path:polygon(12% 0,100% 0,100% 100%,0 100%)"></div>
  <h1 class="abs" style="left:155px;top:120px;margin:0;color:#fff;font-size:19px;line-height:1.05;font-weight:600;text-align:center">Presentation<br>Title Goes Here</h1>
</section>

<section class="slide">
  <div class="faint-name" style="right:22px;top:44px;font-size:22px;line-height:1.05;text-align:center">Ledger<br>Lanternfox</div>
  <div class="abs" style="left:24px;top:40px">
    <span class="brand">Ledger Lanternfox</span>
    <h1 style="margin:14px 0 0;font-size:22px;line-height:1.02;font-weight:600;color:var(--navy);position:relative">Presentation<br>Title Goes Here</h1>
    <p style="margin:2px 0 0;font-size:7px;color:var(--red)">Sub Title Goes Here</p>
    <span class="pill" style="margin-top:18px;font-size:5px;padding:3px 12px">www.ledgerlanternfox.example</span>
  </div>
</section>

<section class="slide"><div class="abs" style="top:22px;left:0;right:0;text-align:center"><span class="brand">Ledger Lanternfox</span></div></section>
<section class="slide bg-navy"><div class="abs" style="top:22px;left:0;right:0;text-align:center"><span class="brand on-dark">Ledger Lanternfox</span></div></section>
<section class="slide bg-dark"><div class="abs" style="top:22px;left:0;right:0;text-align:center"><span class="brand on-dark">Ledger Lanternfox</span></div></section>
<section class="slide bg-red"><div class="abs" style="top:22px;left:0;right:0;text-align:center"><span class="brand on-dark">Ledger Lanternfox</span></div></section>

<section class="slide">
  <div class="abs" style="left:0;right:22px;top:52px;text-align:center;font-size:52px;color:#cfcfcf;font-weight:700;line-height:1">&ldquo;</div>
  <span class="pill abs" style="left:58px;top:146px;font-size:6px">Your Name</span>
  <div class="rail"><span>Ledger Lanternfox</span></div><span class="num">10</span>
</section>

<section class="slide">
  <div class="abs" role="img" aria-label="Decorative navy accent shape behind the profile photo" style="left:18px;top:40px;width:76px;height:76px;border-radius:50%;background:var(--navy);opacity:.85"></div>
  <div class="abs" role="img" aria-label="Round profile photo" style="left:46px;top:60px;width:68px;height:68px;border-radius:50%;background:#d3d3d3;box-shadow:0 3px 8px rgba(0,0,0,.18)"></div>
  <div class="dash" style="left:156px;top:61px"></div>
  <div class="abs" style="left:40px;top:150px;display:flex;flex-direction:column;gap:6px">
    <span style="width:5px;height:5px;border-radius:50%;background:var(--navy)"></span>
    <span style="width:5px;height:5px;border-radius:50%;background:var(--navy)"></span>
    <span style="width:5px;height:5px;border-radius:50%;background:var(--navy)"></span>
  </div>
  <div class="rail"><span>Ledger Lanternfox</span></div><span class="num">11</span>
</section>

<section class="slide">
  <div class="abs bg-navy" style="left:0;top:0;width:116px;height:106px"></div>
  <div class="abs" style="left:34px;top:32px;width:168px;height:150px;background:#fff;box-shadow:0 2px 10px rgba(0,0,0,.15);padding:14px 18px">
    <ol style="margin:0;padding-left:12px;font-size:6px;line-height:2.45;color:var(--navy)">
      <li>Lorem ipsum dolor sit amet</li><li>Lorem ipsum dolor sit amet</li><li>Lorem ipsum dolor sit amet</li><li>Lorem ipsum dolor sit amet</li><li>Lorem ipsum dolor sit amet</li><li>Lorem ipsum dolor sit amet</li><li>Lorem ipsum dolor sit amet</li>
    </ol>
  </div>
  <div class="abs" style="left:228px;top:76px">
    <h2 style="margin:0;font-size:12.5px;line-height:1.1;font-weight:600;color:var(--navy)">Here Goes<br>Title Of Your<br>Agenda</h2>
    <p style="margin:2px 0 0;font-size:5px;color:var(--red)">Here Goes A Short Subtitle</p>
  </div>
  <div class="rail"><span>Ledger Lanternfox</span></div><span class="num">12</span>
</section>

<section class="slide">
  <h2 class="h-left" style="left:14px;top:10px">Title And Body Slide</h2>
  <div class="faint-name" style="left:140px;top:90px;font-size:28px">Ledger Lanternfox</div>
  <div class="rail"><span>Ledger Lanternfox</span></div><span class="num">13</span>
</section>

<section class="slide">
  <div class="dash" style="left:32px;top:36px"></div>
  <div class="rail left"><span>Ledger Lanternfox</span></div>
  <div class="faint-name" style="left:130px;top:90px;font-size:28px">Ledger Lanternfox</div>
  <span class="num ll">14</span>
  <div style="position:absolute;top:6px;right:6px;width:10px;height:10px;border-radius:50%;background:var(--navy)"></div>
</section>

<section class="slide">
  <h2 class="h-left" style="left:18px;top:10px">Title And Body Slide</h2>
  <div class="rail"><span>Ledger Lanternfox</span></div><span class="num">15</span>
</section>

<section class="slide">
  <div class="dash" style="left:28px;top:34px"></div>
  <div class="rail left"><span>Ledger Lanternfox</span></div><span class="num ll">16</span>
</section>

<section class="slide bg-navy">
  <h2 class="h-left" style="left:18px;top:10px;color:#fff">Title And Body Slide</h2>
  <div class="rail dark"><span>Ledger Lanternfox</span></div><span class="num" style="color:#cbd4e6">17</span>
</section>

<section class="slide bg-navy">
  <div class="dash" style="left:32px;top:36px"></div>
  <div class="rail left dark"><span>Ledger Lanternfox</span></div><span class="num ll" style="color:#cbd4e6">18</span>
</section>

<section class="slide">
  <div class="dash" style="left:14px;top:36px"></div>
  <div class="rail"><span>Ledger Lanternfox</span></div>
</section>

<section class="slide">
  <div class="dash" style="left:28px;top:36px"></div>
  <div class="rail left"><span>Ledger Lanternfox</span></div><span class="num ll">20</span>
</section>

<section class="slide">
  <div class="abs" style="left:0;right:0;top:86px;text-align:center;font-size:24px;font-weight:700;color:var(--navy);padding-left:150px">Ledger<br>Lanternfox</div>
  <div class="abs" style="left:0;right:0;bottom:0;height:8px;background:var(--red)"></div>
</section>

<section class="slide bg-navy">
  <div class="photo photo-city" role="img" aria-label="Blue toned photo behind the section title" style="opacity:.6"></div>
  <div class="abs" style="left:24px;top:50px;color:#fff">
    <div style="font-size:42px;font-weight:700;opacity:.25;line-height:.8">01</div>
    <div style="margin-top:-20px;font-size:27px;font-weight:300;line-height:1">Slide<br>Break</div>
    <p class="fine w" style="width:170px;margin-top:6px">Short section intro text goes here. Add a line or two about the next part of the talk and what the room will learn from it.</p>
  </div>
</section>

<section class="slide">
  <div class="photo photo-city" role="img" aria-label="Blue toned photo of a keyboard behind the demo circle"></div>
  <div class="abs" style="left:102px;top:16px;width:182px;height:182px;border:1px solid rgba(255,255,255,.8);border-radius:50%;text-align:center;padding:40px 24px 0;color:#fff">
    <div style="font-size:15px;font-weight:600;color:var(--red)">— DEMO —</div>
    <p class="fine w" style="font-size:5px;margin-top:6px">A live demo comes next. Watch each step on screen as we build it, then try it on your own data. Short notes for the demo go in this circle so the room can follow along with ease.</p>
  </div>
</section>

<section class="slide bg-navy">
  <div class="abs" style="left:82px;top:8px;width:200px;height:200px;border-radius:50%;background:var(--navy-deep);opacity:.7"></div>
  <div class="abs" style="left:102px;top:16px;width:182px;height:182px;border:1px solid rgba(255,255,255,.8);border-radius:50%;text-align:center;padding:40px 24px 0;color:#fff">
    <div style="font-size:15px;font-weight:600">— DEMO —</div>
    <p class="fine w" style="font-size:5px;margin-top:6px">A live demo comes next. Watch each step on screen as we build it, then try it on your own data. Short notes for the demo go in this circle so the room can follow along with ease.</p>
  </div>
</section>

<section class="slide">
  <div class="photo photo-city" role="img" aria-label="Blue toned photo of a laptop behind the demo text"></div>
  <div class="abs" style="left:12px;right:12px;top:26px;border-top:1px solid rgba(255,255,255,.3);border-bottom:1px solid rgba(255,255,255,.3);height:166px"></div>
  <div class="abs" style="left:16px;top:98px"><span class="brand on-dark">Ledger Lanternfox</span></div>
  <div class="abs" style="left:166px;top:68px;width:200px;color:#fff">
    <span class="pill" style="font-size:8px;padding:2px 12px">DEMO</span>
    <p style="font-size:6px;line-height:1.4;margin:6px 0 0;opacity:.9">Now we switch to a live demo. Follow along as each query runs and the results load. Questions are welcome at the end of this part, so note them as we go along.</p>
  </div>
</section>

<section class="slide">
  <h2 class="h-left" style="left:20px;top:60px;font-size:18px">Pic And Text</h2>
  <p class="fine" style="position:absolute;left:20px;top:96px;width:134px;font-size:5.2px;text-align:justify">Add a short paragraph here that explains the picture. Keep it to a few lines so the text stays large and easy to read from the back row. One clear idea per slide works best for a room full of people.</p>
  <div class="abs bg-red" style="left:190px;top:24px;width:100px;height:40px"></div>
  <div class="abs" role="img" aria-label="Photo of hands typing on a laptop at a desk" style="left:198px;top:34px;width:162px;height:144px;background:linear-gradient(135deg,#c9ccd4,#8a90a0 50%,#4b5060)"></div>
  <div class="rail"><span>Ledger Lanternfox</span></div><span class="num">24</span>
</section>

<section class="slide">
  <div class="abs bg-red" style="left:190px;top:60px;width:44px;height:2px"></div>
  <div class="abs bg-navy" style="left:88px;right:22px;bottom:0;height:72px;border-top-left-radius:36px"></div>
  <div class="rail"><span>Ledger Lanternfox</span></div>
</section>

<section class="slide">
  <div class="abs bg-navy" style="left:0;right:22px;top:0;height:110px"></div>
  <h2 class="h-title" style="color:#fff;top:30px">Here Add Awesome Text</h2>
  <div class="abs" style="left:0;right:22px;top:92px;display:flex;justify-content:space-around;text-align:center">
    <div style="width:100px">
      <div style="width:36px;height:36px;border-radius:50%;background:var(--red);border:3px solid #fff;margin:0 auto"><svg width="30" height="30" viewBox="0 0 30 30"><circle cx="15" cy="15" r="6" fill="none" stroke="#fff" stroke-width="1.5"/><circle cx="15" cy="15" r="2" fill="#fff"/></svg></div>
      <b style="display:block;font-size:6px;margin:6px 0 2px">Project name</b>
      <p class="fine">Short note on the project goes here in a few words and a line.</p>
    </div>
    <div style="width:100px">
      <div style="width:36px;height:36px;border-radius:50%;background:var(--red);border:3px solid #fff;margin:0 auto"><svg width="30" height="30" viewBox="0 0 30 30"><path d="M10 20l10-10M14 10h6v6" fill="none" stroke="#fff" stroke-width="1.5"/></svg></div>
      <b style="display:block;font-size:6px;margin:6px 0 2px">Project name</b>
      <p class="fine">Short note on the project goes here in a few words and a line.</p>
    </div>
    <div style="width:100px">
      <div style="width:36px;height:36px;border-radius:50%;background:var(--red);border:3px solid #fff;margin:0 auto"><svg width="30" height="30" viewBox="0 0 30 30"><rect x="9" y="9" width="12" height="12" fill="none" stroke="#fff" stroke-width="1.5"/><path d="M12 15h6" stroke="#fff" stroke-width="1.5"/></svg></div>
      <b style="display:block;font-size:6px;margin:6px 0 2px">Project name</b>
      <p class="fine">Short note on the project goes here in a few words and a line.</p>
    </div>
  </div>
  <div class="rail"><span>Ledger Lanternfox</span></div><span class="num ll">28</span>
</section>

<section class="slide">
  <h2 class="h-title">3 Columns Slide</h2>
  <div class="card" style="left:42px;top:92px;width:90px;height:82px;background:var(--red)"><b>Project name here</b><p>Short text about this item goes here in two lines.</p></div>
  <div class="card" style="left:140px;top:92px;width:90px;height:82px;background:var(--navy)"><b>Project name here</b><p>Short text about this item goes here in two lines.</p></div>
  <div class="card" style="left:238px;top:92px;width:90px;height:82px;background:var(--gray)"><b>Project name here</b><p>Short text about this item goes here in two lines.</p></div>
  <svg class="abs" style="left:78px;top:76px" width="250" height="20" viewBox="0 0 250 20"><circle cx="10" cy="10" r="5" fill="none" stroke="var(--red)" stroke-width="1.3"/><circle cx="108" cy="10" r="5" fill="none" stroke="var(--navy)" stroke-width="1.3"/><circle cx="206" cy="10" r="5" fill="none" stroke="var(--gray)" stroke-width="1.3"/></svg>
  <div class="rail"><span>Ledger Lanternfox</span></div><span class="num">29</span>
</section>

<section class="slide">
  <h2 class="h-title">4 Column Slide</h2>
  <div class="card" style="left:20px;top:70px;width:80px;height:118px;background:var(--red)"><b>Project name here</b><p>Short text about this item goes here. It can run over a few short lines of copy.</p></div>
  <div class="card" style="left:106px;top:70px;width:80px;height:118px;background:var(--navy)"><b>Project name here</b><p>Short text about this item goes here. It can run over a few short lines of copy.</p></div>
  <div class="card" style="left:192px;top:70px;width:80px;height:118px;background:#243a5a"><b>Project name here</b><p>Short text about this item goes here. It can run over a few short lines of copy.</p></div>
  <div class="card" style="left:278px;top:70px;width:80px;height:118px;background:var(--gray)"><b>Project name here</b><p>Short text about this item goes here. It can run over a few short lines of copy.</p></div>
  <svg class="abs" style="left:48px;top:60px" width="290" height="22" viewBox="0 0 290 22"><circle cx="12" cy="11" r="9" fill="#fff"/><circle cx="98" cy="11" r="9" fill="#fff"/><circle cx="184" cy="11" r="9" fill="#fff"/><circle cx="270" cy="11" r="9" fill="#fff"/><circle cx="12" cy="11" r="4" fill="none" stroke="var(--red)"/><circle cx="98" cy="11" r="4" fill="none" stroke="var(--navy)"/><circle cx="184" cy="11" r="4" fill="none" stroke="#243a5a"/><circle cx="270" cy="11" r="4" fill="none" stroke="var(--gray)"/></svg>
  <div class="rail"><span>Ledger Lanternfox</span></div><span class="num">30</span>
</section>

<section class="slide">
  <h2 class="h-title">5 Column Slide</h2>
  <div class="card" style="left:42px;top:68px;width:92px;height:56px;background:var(--navy);padding-top:6px"><b>Project name here</b><p>Short text about this item goes here in a line or two.</p></div>
  <div class="card" style="left:140px;top:68px;width:92px;height:56px;background:var(--navy);padding-top:6px"><b>Project name here</b><p>Short text about this item goes here in a line or two.</p></div>
  <div class="card" style="left:238px;top:68px;width:92px;height:56px;background:var(--navy);padding-top:6px"><b>Project name here</b><p>Short text about this item goes here in a line or two.</p></div>
  <div class="card" style="left:91px;top:132px;width:92px;height:56px;background:var(--navy);padding-top:6px"><b>Project name here</b><p>Short text about this item goes here in a line or two.</p></div>
  <div class="card" style="left:189px;top:132px;width:92px;height:56px;background:var(--navy);padding-top:6px"><b>Project name here</b><p>Short text about this item goes here in a line or two.</p></div>
  <div class="rail"><span>Ledger Lanternfox</span></div><span class="num">31</span>
</section>

<section class="slide">
  <div class="abs bg-navy" style="left:0;top:0;bottom:0;width:220px;clip-path:polygon(0 0,60% 0,100% 100%,0 100%)"></div>
  <div class="abs" style="left:18px;top:68px;color:#fff">
    <h2 style="margin:0;font-size:13px;line-height:1.15;font-weight:600">A Place for<br>Screenshot</h2>
    <div style="width:14px;height:2px;background:var(--red);margin-top:3px"></div>
    <p class="fine w" style="width:118px;margin-top:5px">Drop a screenshot of the tool or query in the laptop screen to show it in use.</p>
  </div>
  <div class="abs" style="left:154px;top:46px;width:196px;height:120px;background:#1a1a1a;border-radius:5px;padding:6px">
    <div style="width:100%;height:100%;background:#8a8a8a;display:flex;align-items:center;justify-content:center;color:#fff;font-size:6px;font-weight:500">HERE YOU CAN ADD A SCREENSHOT</div>
  </div>
  <div class="abs" style="left:140px;top:166px;width:224px;height:7px;background:linear-gradient(#d8d8d8,#9a9a9a);border-radius:0 0 6px 6px"></div>
  <div class="rail"><span>Ledger Lanternfox</span></div><span class="num">32</span>
</section>

<section class="slide">
  <h2 class="h-title">6 Columns Slide</h2>
  <div class="abs" style="left:26px;top:70px;width:320px;display:grid;grid-template-columns:1fr 1fr;row-gap:18px;column-gap:30px">
    <div style="display:flex;gap:8px"><svg width="14" height="14" viewBox="0 0 14 14"><rect x="2" y="2" width="10" height="10" fill="none" stroke="var(--gray)"/></svg><div><b style="font-size:5.5px;font-weight:600">Project name</b><p class="fine" style="font-size:4px">Short text about this item goes here in a line or two.</p></div></div>
    <div style="display:flex;gap:8px"><svg width="14" height="14" viewBox="0 0 14 14"><rect x="3" y="1" width="8" height="12" fill="none" stroke="var(--gray)"/></svg><div><b style="font-size:5.5px;font-weight:600">Project name</b><p class="fine" style="font-size:4px">Short text about this item goes here in a line or two.</p></div></div>
    <div style="display:flex;gap:8px"><svg width="14" height="14" viewBox="0 0 14 14"><path d="M2 12V8M6 12V5M10 12V2" stroke="var(--gray)" stroke-width="1.5"/></svg><div><b style="font-size:5.5px;font-weight:600">Project name</b><p class="fine" style="font-size:4px">Short text about this item goes here in a line or two.</p></div></div>
    <div style="display:flex;gap:8px"><svg width="14" height="14" viewBox="0 0 14 14"><path d="M2 12V8M6 12V5M10 12V2" stroke="var(--gray)" stroke-width="1.5"/></svg><div><b style="font-size:5.5px;font-weight:600">Project name</b><p class="fine" style="font-size:4px">Short text about this item goes here in a line or two.</p></div></div>
    <div style="display:flex;gap:8px"><svg width="14" height="14" viewBox="0 0 14 14"><circle cx="7" cy="7" r="5" fill="none" stroke="var(--gray)"/></svg><div><b style="font-size:5.5px;font-weight:600">Project name</b><p class="fine" style="font-size:4px">Short text about this item goes here in a line or two.</p></div></div>
    <div style="display:flex;gap:8px"><svg width="14" height="14" viewBox="0 0 14 14"><circle cx="7" cy="7" r="5" fill="none" stroke="var(--gray)"/></svg><div><b style="font-size:5.5px;font-weight:600">Project name</b><p class="fine" style="font-size:4px">Short text about this item goes here in a line or two.</p></div></div>
  </div>
  <div class="rail"><span>Ledger Lanternfox</span></div><span class="num">33</span>
</section>

<section class="slide">
  <h2 class="h-title">Table Slide</h2>
  <table class="grid abs" style="left:18px;top:56px;width:330px;text-align:center;color:#777">
    <tr style="height:12px"><td style="width:90px"></td><td style="background:var(--red);color:#fff">Your Text Here</td><td style="background:var(--red);color:#fff">Your Text Here</td><td style="background:var(--red);color:#fff">Your Text Here</td><td style="background:var(--red);color:#fff">Your Text Here</td></tr>
    <tr style="height:17px;border-bottom:1px solid #eee"><td style="background:var(--navy);color:#fff;text-align:left;padding-left:4px;font-weight:600">You can replace this text</td><td>1200</td><td><b style="color:var(--navy)">✔</b></td><td>80%</td><td>1500</td></tr>
    <tr style="height:17px;border-bottom:1px solid #eee"><td style="background:var(--navy);color:#fff;text-align:left;padding-left:4px;font-weight:600">You can replace this text</td><td>3620</td><td><b style="color:var(--navy)">✖</b></td><td>50%</td><td>3620</td></tr>
    <tr style="height:17px;border-bottom:1px solid #eee"><td style="background:var(--navy);color:#fff;text-align:left;padding-left:4px;font-weight:600">You can replace this text</td><td>2560</td><td><b style="color:var(--navy)">✔</b></td><td>12%</td><td>2560</td></tr>
    <tr style="height:17px;border-bottom:1px solid #eee"><td style="background:var(--navy);color:#fff;text-align:left;padding-left:4px;font-weight:600">You can replace this text</td><td>1320</td><td><b style="color:var(--navy)">✖</b></td><td>63%</td><td>1320</td></tr>
    <tr style="height:17px;border-bottom:1px solid #eee"><td style="background:var(--navy);color:#fff;text-align:left;padding-left:4px;font-weight:600">You can replace this text</td><td>2100</td><td><b style="color:var(--navy)">✔</b></td><td>34%</td><td>2100</td></tr>
    <tr style="height:17px;border-bottom:1px solid #eee"><td style="background:var(--navy);color:#fff;text-align:left;padding-left:4px;font-weight:600">You can replace this text</td><td>1690</td><td><b style="color:var(--navy)">✖</b></td><td>94%</td><td>1690</td></tr>
    <tr style="height:17px"><td style="background:var(--navy);color:#fff;text-align:left;padding-left:4px;font-weight:600">You can replace this text</td><td>1400</td><td><b style="color:var(--navy)">✔</b></td><td>48%</td><td>1990</td></tr>
  </table>
  <div class="rail"><span>Ledger Lanternfox</span></div><span class="num ll">34</span>
</section>

<section class="slide">
  <div class="abs bg-navy" style="left:0;top:0;bottom:0;width:206px"></div>
  <h2 class="h-left" style="left:16px;top:96px;font-size:15px;color:#fff">Table Slide</h2>
  <div class="abs" style="left:134px;top:28px;width:216px;height:162px;background:#fff;box-shadow:0 2px 10px rgba(0,0,0,.15);padding:8px">
    <table class="grid" style="width:100%;text-align:center;color:#999">
      <tr style="height:12px;background:var(--navy);color:#fff"><td>Text</td><td>Text</td><td>Text</td><td>Text</td><td>Text</td></tr>
      <tr style="height:20px;border-bottom:1px solid #eee"><td style="color:var(--navy);font-weight:600">Data</td><td>Data</td><td>Data</td><td>Data</td><td>Data</td></tr>
      <tr style="height:20px;border-bottom:1px solid #eee"><td style="color:var(--navy);font-weight:600">Data</td><td>Data</td><td>Data</td><td>Data</td><td>Data</td></tr>
      <tr style="height:20px;border-bottom:1px solid #eee"><td style="color:var(--navy);font-weight:600">Data</td><td>Data</td><td>Data</td><td>Data</td><td>Data</td></tr>
      <tr style="height:20px;border-bottom:1px solid #eee"><td style="color:var(--navy);font-weight:600">Data</td><td>Data</td><td>Data</td><td>Data</td><td>Data</td></tr>
      <tr style="height:20px;border-bottom:1px solid #eee"><td style="color:var(--navy);font-weight:600">Data</td><td>Data</td><td>Data</td><td>Data</td><td>Data</td></tr>
      <tr style="height:20px"><td style="color:var(--navy);font-weight:600">Data</td><td>Data</td><td>Data</td><td>Data</td><td>Data</td></tr>
    </table>
  </div>
  <div class="rail"><span>Ledger Lanternfox</span></div><span class="num">35</span>
</section>

<section class="slide">
  <h2 class="h-title">Table Slide</h2>
  <table class="grid abs" style="left:30px;top:68px;width:318px;text-align:center;color:#999">
    <tr style="height:12px;background:var(--navy);color:#fff"><td>Text</td><td>Text</td><td>Text</td><td>Text</td><td>Text</td></tr>
    <tr style="height:18px;border-bottom:1px solid #eee"><td style="color:var(--navy);font-weight:600">Data</td><td>Data</td><td>Data</td><td>Data</td><td>Data</td></tr>
    <tr style="height:18px;border-bottom:1px solid #eee"><td style="color:var(--navy);font-weight:600">Data</td><td>Data</td><td>Data</td><td>Data</td><td>Data</td></tr>
    <tr style="height:18px;border-bottom:1px solid #eee"><td style="color:var(--navy);font-weight:600">Data</td><td>Data</td><td>Data</td><td>Data</td><td>Data</td></tr>
    <tr style="height:18px;border-bottom:1px solid #eee"><td style="color:var(--navy);font-weight:600">Data</td><td>Data</td><td>Data</td><td>Data</td><td>Data</td></tr>
    <tr style="height:18px;border-bottom:1px solid #eee"><td style="color:var(--navy);font-weight:600">Data</td><td>Data</td><td>Data</td><td>Data</td><td>Data</td></tr>
    <tr style="height:18px"><td style="color:var(--navy);font-weight:600">Data</td><td>Data</td><td>Data</td><td>Data</td><td>Data</td></tr>
  </table>
  <div class="rail"><span>Ledger Lanternfox</span></div><span class="num">36</span>
</section>

<section class="slide">
  <h2 class="h-left" style="left:20px;top:8px">Smart Art Slide</h2>
  <div class="abs" style="left:20px;top:60px;width:150px;display:flex;flex-direction:column;gap:14px">
    <div style="display:flex;gap:6px"><svg width="14" height="14" viewBox="0 0 14 14"><circle cx="7" cy="7" r="5" fill="none" stroke="var(--gray)"/></svg><div><b style="font-size:5.5px;font-weight:600;color:var(--navy)">Lorem ipsum dolor</b><p class="fine" style="font-size:4px">Short line of text that explains this point in brief words here.</p></div></div>
    <div style="display:flex;gap:6px"><svg width="14" height="14" viewBox="0 0 14 14"><path d="M2 12L12 2M8 2h4v4" fill="none" stroke="var(--gray)"/></svg><div><b style="font-size:5.5px;font-weight:600;color:var(--navy)">Lorem ipsum dolor</b><p class="fine" style="font-size:4px">Short line of text that explains this point in brief words here.</p></div></div>
    <div style="display:flex;gap:6px"><svg width="14" height="14" viewBox="0 0 14 14"><rect x="2" y="2" width="10" height="10" fill="none" stroke="var(--gray)"/></svg><div><b style="font-size:5.5px;font-weight:600;color:var(--navy)">Lorem ipsum dolor</b><p class="fine" style="font-size:4px">Short line of text that explains this point in brief words here.</p></div></div>
  </div>
  <svg class="abs" style="left:200px;top:40px" width="160" height="150" viewBox="0 0 160 150">
    <polygon points="80,4 118,72 42,72" fill="var(--navy)"/>
    <polygon points="38,78 76,78 38,146 0,146" fill="var(--red)" transform="translate(4,0)"/>
    <polygon points="84,78 122,78 160,146 122,146" fill="var(--gray)" transform="translate(-4,0)"/>
    <text x="80" y="48" text-anchor="middle" font-size="5" font-weight="600" fill="#fff" font-family="Poppins, sans-serif">Project</text>
    <text x="80" y="55" text-anchor="middle" font-size="5" font-weight="600" fill="#fff" font-family="Poppins, sans-serif">name</text>
    <text x="46" y="104" text-anchor="middle" font-size="5" font-weight="600" fill="#fff" font-family="Poppins, sans-serif">Project name</text>
    <text x="114" y="104" text-anchor="middle" font-size="5" font-weight="600" fill="#fff" font-family="Poppins, sans-serif">Project name</text>
  </svg>
  <div class="rail"><span>Ledger Lanternfox</span></div><span class="num">37</span>
</section>

<section class="slide">
  <h2 class="h-title">Here is Quotes</h2>
  <div class="abs" style="left:28px;top:66px;width:140px">
    <div class="q-mark">&rdquo;</div>
    <p style="font-size:5.5px;line-height:1.5;color:#555;margin:8px 0 12px">A short quote goes here. Keep it to a few lines so it reads well from the back of the room and makes one clear point.</p>
    <div style="display:flex;align-items:center;gap:5px"><span style="width:14px;height:14px;border-radius:50%;background:#ddd"></span><span style="font-size:4.5px;color:#555">Your Name<br>Founder</span></div>
  </div>
  <div class="abs" style="left:200px;top:66px;width:140px">
    <div class="q-mark" style="color:var(--navy)">&rdquo;</div>
    <p style="font-size:5.5px;line-height:1.5;color:#555;margin:8px 0 12px">A short quote goes here. Keep it to a few lines so it reads well from the back of the room and makes one clear point.</p>
    <div style="display:flex;align-items:center;gap:5px"><span style="width:14px;height:14px;border-radius:50%;background:#ddd"></span><span style="font-size:4.5px;color:#555">Your Name<br>Founder</span></div>
  </div>
  <div class="rail"><span>Ledger Lanternfox</span></div><span class="num">38</span>
</section>

<section class="slide">
  <h2 class="h-title">Here Is Statistics</h2>
  <svg class="abs" style="left:22px;top:62px" width="170" height="130" viewBox="0 0 170 130">
    <circle cx="60" cy="62" r="56" fill="var(--navy)"/>
    <circle cx="60" cy="62" r="38" fill="var(--red)"/>
    <circle cx="60" cy="62" r="20" fill="#555"/>
    <line x1="60" y1="6" x2="150" y2="6" stroke="#ccc" stroke-width=".6"/>
    <line x1="60" y1="28" x2="150" y2="28" stroke="#ccc" stroke-width=".6"/>
    <text x="60" y="27" text-anchor="middle" font-size="12" font-weight="700" fill="#fff" font-family="Poppins, sans-serif">$</text>
    <text x="60" y="60" text-anchor="middle" font-size="11" font-weight="700" fill="#fff" font-family="Poppins, sans-serif">$</text>
    <text x="60" y="88" text-anchor="middle" font-size="9" font-weight="700" fill="#fff" font-family="Poppins, sans-serif">$</text>
    <text x="132" y="20" font-size="9" font-weight="600" fill="#2a2a2a" font-family="Poppins, sans-serif">5M</text>
    <text x="132" y="56" font-size="9" font-weight="600" fill="#2a2a2a" font-family="Poppins, sans-serif">2M</text>
    <text x="132" y="96" font-size="9" font-weight="600" fill="#2a2a2a" font-family="Poppins, sans-serif">1M</text>
  </svg>
  <div class="abs" style="left:218px;top:70px;width:130px;display:flex;flex-direction:column;gap:10px">
    <div style="display:flex;gap:6px"><span style="width:11px;height:11px;background:var(--navy);color:#fff;font-size:8px;line-height:11px;text-align:center;flex:none">✓</span><div><b style="font-size:5.5px;font-weight:600">Lorem ipsum dolor</b><p class="fine" style="font-size:4px">Short line of text for this point in brief.</p></div></div>
    <div style="display:flex;gap:6px"><span style="width:11px;height:11px;background:var(--red);color:#fff;font-size:8px;line-height:11px;text-align:center;flex:none">✓</span><div><b style="font-size:5.5px;font-weight:600">Lorem ipsum dolor</b><p class="fine" style="font-size:4px">Short line of text for this point in brief.</p></div></div>
    <div style="display:flex;gap:6px"><span style="width:11px;height:11px;background:#555;color:#fff;font-size:8px;line-height:11px;text-align:center;flex:none">✓</span><div><b style="font-size:5.5px;font-weight:600">Lorem ipsum dolor</b><p class="fine" style="font-size:4px">Short line of text for this point in brief.</p></div></div>
  </div>
  <div class="rail"><span>Ledger Lanternfox</span></div><span class="num">39</span>
</section>

<section class="slide">
  <h2 class="h-title">Here Add Your Title</h2>
  <p class="fine abs" style="left:60px;right:80px;top:58px;text-align:center;font-size:4.6px">Add a short lead paragraph here that sets up the three numbers below. Keep it brief and clear so the room can read it at a glance before you talk through each result one by one.</p>
  <svg class="abs" style="left:70px;top:96px" width="240" height="60" viewBox="0 0 240 60" font-family="Poppins, sans-serif">
    <circle cx="30" cy="28" r="22" fill="none" stroke="#eee" stroke-width="5"/>
    <circle cx="30" cy="28" r="22" fill="none" stroke="#1f4182" stroke-width="5" stroke-dasharray="69 138" transform="rotate(-90 30 28)"/>
    <text x="30" y="32" text-anchor="middle" font-size="11" font-weight="600" fill="#1f4182">50%</text>
    <circle cx="114" cy="28" r="22" fill="none" stroke="#eee" stroke-width="5"/>
    <circle cx="114" cy="28" r="22" fill="none" stroke="#e8312c" stroke-width="5" stroke-dasharray="104 138" transform="rotate(-90 114 28)"/>
    <text x="114" y="32" text-anchor="middle" font-size="11" font-weight="600" fill="#e8312c">75%</text>
    <circle cx="198" cy="28" r="22" fill="none" stroke="#eee" stroke-width="5"/>
    <circle cx="198" cy="28" r="22" fill="none" stroke="#1f4182" stroke-width="5" stroke-dasharray="55 138" transform="rotate(-90 198 28)"/>
    <text x="198" y="32" text-anchor="middle" font-size="11" font-weight="600" fill="#1f4182">40%</text>
  </svg>
  <div class="abs" style="left:70px;top:160px;width:240px;display:flex;justify-content:space-between;text-align:center">
    <p class="fine" style="width:60px;font-size:4px">Short note about the result</p><p class="fine" style="width:60px;font-size:4px">Short note about the result</p><p class="fine" style="width:60px;font-size:4px">Short note about the result</p>
  </div>
  <div class="rail"><span>Ledger Lanternfox</span></div>
</section>

<section class="slide">
  <h2 class="h-title">Here is Statistics</h2>
  <div class="abs bg-navy" style="left:16px;top:64px;width:90px;height:56px;color:#fff;text-align:center;padding-top:12px">
    <div style="font-size:14px">$0.5M</div><div style="font-size:4.5px;opacity:.8">Revenue</div>
  </div>
  <div class="abs" style="left:16px;top:124px;width:90px;height:56px;border:1px solid #ddd;color:var(--red);text-align:center;padding-top:12px">
    <div style="font-size:14px">-0.28%</div><div style="font-size:4.5px;opacity:.8">Revenue</div>
  </div>
  <svg class="abs" style="left:118px;top:64px" width="240" height="124" viewBox="0 0 240 124" font-family="Poppins, sans-serif" font-size="4" fill="#888">
    <g stroke="#eee" stroke-width=".5"><line x1="24" y1="6" x2="236" y2="6"/><line x1="24" y1="22" x2="236" y2="22"/><line x1="24" y1="38" x2="236" y2="38"/><line x1="24" y1="54" x2="236" y2="54"/><line x1="24" y1="70" x2="236" y2="70"/><line x1="24" y1="86" x2="236" y2="86"/><line x1="24" y1="102" x2="236" y2="102"/></g>
    <text x="0" y="8">$60,000</text><text x="0" y="24">$50,000</text><text x="0" y="40">$40,000</text><text x="0" y="56">$30,000</text><text x="0" y="72">$20,000</text><text x="0" y="88">$10,000</text><text x="12" y="104">0</text>
    <polyline points="30,100 48,96 66,86 84,92 102,78 120,84 138,74 156,80 174,66 192,70 210,50 228,18" fill="none" stroke="#e8312c" stroke-width="1.2"/>
    <text x="28" y="114">Jan</text><text x="46" y="114">Feb</text><text x="64" y="114">Mar</text><text x="82" y="114">Apr</text><text x="100" y="114">May</text><text x="118" y="114">Jun</text><text x="136" y="114">Jul</text><text x="154" y="114">Aug</text><text x="172" y="114">Sep</text><text x="190" y="114">Oct</text><text x="208" y="114">Nov</text><text x="226" y="114">Dec</text>
  </svg>
  <div class="rail"><span>Ledger Lanternfox</span></div><span class="num">41</span>
</section>

<section class="slide">
  <h2 class="h-title">Company Timeline</h2>
  <svg class="abs" style="left:22px;top:86px" width="330" height="30" viewBox="0 0 330 30" font-family="Poppins, sans-serif">
    <g fill="#e8312c">
      <polygon points="0,2 52,2 62,15 52,28 0,28 8,15"/>
      <polygon points="62,2 114,2 124,15 114,28 62,28 70,15"/>
      <polygon points="124,2 176,2 186,15 176,28 124,28 132,15"/>
      <polygon points="186,2 238,2 248,15 238,28 186,28 194,15"/>
      <polygon points="248,2 300,2 310,15 300,28 248,28 256,15"/>
    </g>
    <g fill="#fff" font-size="6" font-weight="600" text-anchor="middle">
      <text x="33" y="17">STEP 01</text><text x="95" y="17">STEP 02</text><text x="157" y="17">STEP 03</text><text x="219" y="17">STEP 04</text><text x="281" y="17">STEP 05</text>
    </g>
  </svg>
  <div class="abs" style="left:22px;top:124px;width:320px;display:flex;justify-content:space-between;text-align:center">
    <div style="width:58px"><b style="font-size:5px;font-weight:600">Project name</b><p class="fine" style="font-size:4px">A short line on this step of the plan here.</p></div>
    <div style="width:58px"><b style="font-size:5px;font-weight:600">Project name</b><p class="fine" style="font-size:4px">A short line on this step of the plan here.</p></div>
    <div style="width:58px"><b style="font-size:5px;font-weight:600">Project name</b><p class="fine" style="font-size:4px">A short line on this step of the plan here.</p></div>
    <div style="width:58px"><b style="font-size:5px;font-weight:600">Project name</b><p class="fine" style="font-size:4px">A short line on this step of the plan here.</p></div>
    <div style="width:58px"><b style="font-size:5px;font-weight:600">Project name</b><p class="fine" style="font-size:4px">A short line on this step of the plan here.</p></div>
  </div>
  <div class="rail"><span>Ledger Lanternfox</span></div><span class="num">42</span>
</section>

<section class="slide">
  <h2 class="h-title">Q&amp;A Slide</h2>
  <div class="abs" style="left:40px;top:64px;width:300px;display:grid;grid-template-columns:1fr 1fr;row-gap:12px;column-gap:24px">
    <div style="display:flex;gap:8px"><span style="width:18px;height:18px;background:var(--navy);color:#fff;font-size:8px;font-weight:700;text-align:center;line-height:18px;flex:none">Q</span><p class="fine" style="font-size:4.5px">A short question goes here on one or two lines.</p></div>
    <div style="display:flex;gap:8px"><span style="width:18px;height:18px;background:var(--red);color:#fff;font-size:8px;font-weight:700;text-align:center;line-height:18px;flex:none">A</span><p class="fine" style="font-size:4.5px">A short answer goes here on one or two lines.</p></div>
    <div style="display:flex;gap:8px"><span style="width:18px;height:18px;background:var(--navy);color:#fff;font-size:8px;font-weight:700;text-align:center;line-height:18px;flex:none">Q</span><p class="fine" style="font-size:4.5px">A short question goes here on one or two lines.</p></div>
    <div style="display:flex;gap:8px"><span style="width:18px;height:18px;background:var(--red);color:#fff;font-size:8px;font-weight:700;text-align:center;line-height:18px;flex:none">A</span><p class="fine" style="font-size:4.5px">A short answer goes here on one or two lines.</p></div>
    <div style="display:flex;gap:8px"><span style="width:18px;height:18px;background:var(--navy);color:#fff;font-size:8px;font-weight:700;text-align:center;line-height:18px;flex:none">Q</span><p class="fine" style="font-size:4.5px">A short question goes here on one or two lines.</p></div>
    <div style="display:flex;gap:8px"><span style="width:18px;height:18px;background:var(--red);color:#fff;font-size:8px;font-weight:700;text-align:center;line-height:18px;flex:none">A</span><p class="fine" style="font-size:4.5px">A short answer goes here on one or two lines.</p></div>
    <div style="display:flex;gap:8px"><span style="width:18px;height:18px;background:var(--navy);color:#fff;font-size:8px;font-weight:700;text-align:center;line-height:18px;flex:none">Q</span><p class="fine" style="font-size:4.5px">A short question goes here on one or two lines.</p></div>
    <div style="display:flex;gap:8px"><span style="width:18px;height:18px;background:var(--red);color:#fff;font-size:8px;font-weight:700;text-align:center;line-height:18px;flex:none">A</span><p class="fine" style="font-size:4.5px">A short answer goes here on one or two lines.</p></div>
  </div>
  <div class="rail"><span>Ledger Lanternfox</span></div><span class="num ll">43</span>
</section>

<section class="slide">
  <div class="photo" role="img" aria-label="Very pale grey photo of a building behind the closing text" style="background:linear-gradient(135deg,#fafafa,#eef0f3)"></div>
  <div class="abs" style="left:44px;top:46px;width:104px;height:124px;background:#fff;box-shadow:0 2px 10px rgba(0,0,0,.12)">
    <div style="padding:10px 0 8px;text-align:center"><span class="brand" style="font-size:7px">Ledger Lanternfox</span></div>
    <div style="background:var(--navy);color:#fff;display:flex;align-items:center;gap:6px;padding:5px 8px;font-size:4.5px"><span style="width:6px;height:6px;border-radius:50%;border:1px solid #fff"></span>www.ledgerlanternfox.example</div>
    <div style="display:flex;align-items:center;gap:6px;padding:8px 8px;font-size:4.5px;color:#777;border-bottom:1px solid #eee"><span style="width:6px;height:6px;border-radius:50%;background:var(--navy)"></span>Find us online<br>Company profile</div>
    <div style="display:flex;align-items:center;gap:6px;padding:8px 8px;font-size:4.5px;color:#777"><span style="width:7px;height:5px;border:1px solid var(--navy)"></span>hello@ledgerlanternfox.example</div>
  </div>
  <h2 class="abs" style="left:200px;top:98px;margin:0;font-size:20px;font-weight:600;color:var(--navy)">THANK YOU</h2>
</section>

<section class="slide">
  <svg class="abs" style="left:86px;top:34px" width="220" height="150" viewBox="0 0 220 150">
    <polygon points="14,14 204,4 196,104 96,110 78,138 74,112 22,116" fill="none" stroke="#1f4182" stroke-width="1.5"/>
    <polygon points="8,20 198,10 190,110 90,116 72,144 68,118 16,122" fill="none" stroke="#e8312c" stroke-width="1.5"/>
    <polygon points="20,22 196,14 188,98 92,104 80,128 78,106 28,108" fill="#fff" stroke="#e6e6e6" stroke-width=".6"/>
  </svg>
  <h2 class="abs" style="left:0;right:0;top:90px;margin:0;text-align:center;font-size:21px;font-weight:600;color:var(--navy)">Questions?</h2>
</section>

<section class="slide">
  <svg class="abs icon-sheet" style="left:20px;top:26px" width="336" height="176" viewBox="0 0 336 176" fill="none" stroke="#3a3a3a" stroke-width="1" stroke-linecap="round" stroke-linejoin="round" aria-label="Set of line icons">
    <defs>
      <symbol id="i-phone" viewBox="0 0 20 20"><rect x="6" y="2" width="8" height="16" rx="1.5"/><path d="M9 15h2"/></symbol>
      <symbol id="i-pin" viewBox="0 0 20 20"><path d="M10 18C5 12 4 10 4 8a6 6 0 0 1 12 0c0 2-1 4-6 10z"/><circle cx="10" cy="8" r="2"/></symbol>
      <symbol id="i-mail" viewBox="0 0 20 20"><rect x="2" y="5" width="16" height="11"/><path d="M2 5l8 6 8-6"/></symbol>
      <symbol id="i-search" viewBox="0 0 20 20"><circle cx="8.5" cy="8.5" r="5.5"/><path d="M12.5 12.5L18 18"/></symbol>
      <symbol id="i-gear" viewBox="0 0 20 20"><circle cx="10" cy="10" r="3"/><circle cx="10" cy="10" r="7" stroke-dasharray="3 2"/></symbol>
      <symbol id="i-chart" viewBox="0 0 20 20"><path d="M3 17h14M6 17v-7M10 17V5M14 17v-4"/></symbol>
      <symbol id="i-db" viewBox="0 0 20 20"><ellipse cx="10" cy="5" rx="6" ry="2.5"/><path d="M4 5v10c0 1.4 2.7 2.5 6 2.5s6-1.1 6-2.5V5M4 10c0 1.4 2.7 2.5 6 2.5s6-1.1 6-2.5"/></symbol>
      <symbol id="i-cloud" viewBox="0 0 20 20"><path d="M6 15h9a3.5 3.5 0 0 0 0-7 5 5 0 0 0-9.6 1A3 3 0 0 0 6 15z"/></symbol>
      <symbol id="i-lock" viewBox="0 0 20 20"><rect x="4" y="9" width="12" height="9"/><path d="M7 9V6a3 3 0 0 1 6 0v3M10 12v3"/></symbol>
      <symbol id="i-cal" viewBox="0 0 20 20"><rect x="3" y="4" width="14" height="13"/><path d="M3 8h14M7 2v4M13 2v4"/></symbol>
      <symbol id="i-tick" viewBox="0 0 20 20"><circle cx="10" cy="10" r="7"/><path d="M6.5 10l2.5 2.5 4.5-5"/></symbol>
      <symbol id="i-monitor" viewBox="0 0 20 20"><rect x="2" y="3" width="16" height="11"/><path d="M7 18h6M10 14v4"/></symbol>
      <symbol id="i-arrow" viewBox="0 0 20 20"><path d="M4 16L16 4M9 4h7v7"/></symbol>
      <symbol id="i-clock" viewBox="0 0 20 20"><circle cx="10" cy="10" r="7"/><path d="M10 6v4l3 2"/></symbol>
      <symbol id="i-bulb" viewBox="0 0 20 20"><path d="M7 13a5 5 0 1 1 6 0v2H7zM8 18h4"/></symbol>
      <symbol id="i-doc" viewBox="0 0 20 20"><path d="M5 2h7l4 4v12H5zM12 2v4h4M8 10h5M8 13h5"/></symbol>
      <symbol id="i-folder" viewBox="0 0 20 20"><path d="M2 6h6l2 2h8v9H2z"/></symbol>
      <symbol id="i-target" viewBox="0 0 20 20"><circle cx="10" cy="10" r="7"/><circle cx="10" cy="10" r="4"/><circle cx="10" cy="10" r="1"/></symbol>
      <symbol id="i-server" viewBox="0 0 20 20"><rect x="3" y="3" width="14" height="5"/><rect x="3" y="11" width="14" height="5"/><path d="M6 5.5h1M6 13.5h1"/></symbol>
      <symbol id="i-share" viewBox="0 0 20 20"><circle cx="5" cy="10" r="2"/><circle cx="15" cy="5" r="2"/><circle cx="15" cy="15" r="2"/><path d="M7 9l6-3M7 11l6 3"/></symbol>
      <symbol id="i-heart" viewBox="0 0 20 20"><path d="M10 17S3 12 3 7.5A3.5 3.5 0 0 1 10 6a3.5 3.5 0 0 1 7 1.5C17 12 10 17 10 17z"/></symbol>
      <symbol id="i-shield" viewBox="0 0 20 20"><path d="M10 2l7 3v5c0 4-3 7-7 8-4-1-7-4-7-8V5z"/></symbol>
    </defs>
    <g>
      <use href="#i-server" x="0" y="0" width="18" height="18"/><use href="#i-db" x="31" y="0" width="18" height="18"/><use href="#i-target" x="62" y="0" width="18" height="18"/><use href="#i-pin" x="93" y="0" width="18" height="18"/><use href="#i-cal" x="124" y="0" width="18" height="18"/><use href="#i-share" x="155" y="0" width="18" height="18"/><use href="#i-doc" x="186" y="0" width="18" height="18"/><use href="#i-lock" x="217" y="0" width="18" height="18"/><use href="#i-phone" x="248" y="0" width="18" height="18"/><use href="#i-mail" x="279" y="0" width="18" height="18"/><use href="#i-arrow" x="310" y="0" width="18" height="18"/>
      <use href="#i-monitor" x="0" y="38" width="18" height="18"/><use href="#i-chart" x="31" y="38" width="18" height="18"/><use href="#i-tick" x="62" y="38" width="18" height="18"/><use href="#i-cloud" x="93" y="38" width="18" height="18"/><use href="#i-gear" x="124" y="38" width="18" height="18"/><use href="#i-folder" x="155" y="38" width="18" height="18"/><use href="#i-clock" x="186" y="38" width="18" height="18"/><use href="#i-bulb" x="217" y="38" width="18" height="18"/><use href="#i-search" x="248" y="38" width="18" height="18"/><use href="#i-heart" x="279" y="38" width="18" height="18"/><use href="#i-shield" x="310" y="38" width="18" height="18"/>
      <use href="#i-target" x="0" y="76" width="18" height="18"/><use href="#i-doc" x="31" y="76" width="18" height="18"/><use href="#i-search" x="62" y="76" width="18" height="18"/><use href="#i-arrow" x="93" y="76" width="18" height="18"/><use href="#i-chart" x="124" y="76" width="18" height="18"/><use href="#i-db" x="155" y="76" width="18" height="18"/><use href="#i-mail" x="186" y="76" width="18" height="18"/><use href="#i-server" x="217" y="76" width="18" height="18"/><use href="#i-lock" x="248" y="76" width="18" height="18"/><use href="#i-share" x="279" y="76" width="18" height="18"/><use href="#i-cloud" x="310" y="76" width="18" height="18"/>
      <use href="#i-folder" x="0" y="114" width="18" height="18"/><use href="#i-chart" x="31" y="114" width="18" height="18"/><use href="#i-clock" x="62" y="114" width="18" height="18"/><use href="#i-gear" x="93" y="114" width="18" height="18"/><use href="#i-cal" x="124" y="114" width="18" height="18"/><use href="#i-heart" x="155" y="114" width="18" height="18"/><use href="#i-monitor" x="186" y="114" width="18" height="18"/><use href="#i-bulb" x="217" y="114" width="18" height="18"/><use href="#i-shield" x="248" y="114" width="18" height="18"/><use href="#i-tick" x="279" y="114" width="18" height="18"/><use href="#i-pin" x="310" y="114" width="18" height="18"/>
      <use href="#i-monitor" x="0" y="152" width="18" height="18"/><use href="#i-phone" x="31" y="152" width="18" height="18"/><use href="#i-cloud" x="62" y="152" width="18" height="18"/><use href="#i-db" x="93" y="152" width="18" height="18"/><use href="#i-mail" x="124" y="152" width="18" height="18"/><use href="#i-search" x="155" y="152" width="18" height="18"/><use href="#i-server" x="186" y="152" width="18" height="18"/><use href="#i-doc" x="217" y="152" width="18" height="18"/><use href="#i-clock" x="248" y="152" width="18" height="18"/><use href="#i-folder" x="279" y="152" width="18" height="18"/>
    </g>
  </svg>
  <div class="rail"><span>Ledger Lanternfox</span></div>
</section>

</main>
</body>
</html>
```